Residential Remodeling Contractor needs updated business card

I need a new design for my business card.
Name of the company is Ridgefell Construction. I need a card that commands presence, strength, integrity. I have been in business for 28 years. I am a Residential Remodeling Contractor that covers all aspects of a residential remodel and build.

```html
<!DOCTYPE html>
<html lang="en">
<head>
<meta charset="utf-8">
<title>Ridgefell Construction – Business Card</title>
<link rel="stylesheet" href="https://fonts.googleapis.com/css2?family=Montserrat:wght@400;500;600;700&display=swap">
<style>
  :root {
    --stage: #e9e8e6;
    --card-blue: #203d85;
    --card-blue-light: #2c4c9a;
    --ink-white: #ffffff;
    --ink-soft: #dfe5f3;
    --rule: rgba(255, 255, 255, 0.45);
  }
  * { box-sizing: border-box; margin: 0; padding: 0; }
  html, body {
    width: 1200px;
    height: 786px;
    overflow: hidden;
    background: var(--stage);
    font-family: "Montserrat", sans-serif;
  }
  .stage {
    width: 1200px;
    height: 786px;
    display: flex;
    align-items: center;
    justify-content: center;
    gap: 40px;
  }
  .card {
    width: 540px;
    height: 309px;
    background: var(--card-blue);
    position: relative;
    box-shadow: 0 6px 18px rgba(0, 0, 0, 0.18);
    color: var(--ink-white);
  }

  /* Front: contact side */
  .card-front { display: flex; align-items: center; }
  .brand {
    width: 250px;
    padding-left: 48px;
    display: flex;
    align-items: center;
    gap: 10px;
  }
  .brand-dot {
    width: 14px;
    height: 14px;
    border-radius: 50%;
    background: var(--ink-white);
    flex: none;
  }
  .brand-name {
    font-weight: 600;
    font-size: 17px;
    line-height: 1.2;
    letter-spacing: 0.08em;
    text-transform: uppercase;
    color: var(--ink-white);
  }
  .divider {
    width: 1px;
    height: 190px;
    background: var(--rule);
  }
  .contact {
    padding-left: 22px;
    display: flex;
    flex-direction: column;
  }
  .person-name { font-weight: 700; font-size: 19px; letter-spacing: 0.01em; }
  .person-role { font-size: 10.5px; color: var(--ink-soft); margin-top: 2px; }
  .address { font-size: 11px; line-height: 1.35; margin-top: 18px; }
  .contact-list { list-style: none; margin-top: 14px; }
  .contact-list li {
    display: flex;
    align-items: center;
    gap: 10px;
    font-size: 11px;
    line-height: 1;
    margin-bottom: 9px;
  }
  .contact-list svg { width: 12px; height: 12px; flex: none; fill: var(--ink-white); }

  /* Back: brand side */
  .card-back {
    overflow: hidden;
    background: linear-gradient(160deg, var(--card-blue-light) 0%, var(--card-blue) 55%);
    display: flex;
    align-items: center;
    justify-content: center;
  }
  .back-name {
    font-weight: 600;
    font-size: 30px;
    line-height: 1.25;
    letter-spacing: 0.1em;
    text-transform: uppercase;
    text-align: center;
    color: var(--ink-soft);
  }
</style>
</head>
<body>
<main class="stage">
  <section class="card card-front" aria-label="Business card, contact side">
    <div class="brand">
      <span class="brand-dot"></span>
      <span class="brand-name">Ridgefell<br>Construction</span>
    </div>
    <div class="divider"></div>
    <div class="contact">
      <p class="person-name">Daniel Hart</p>
      <p class="person-role">Owner</p>
      <p class="address">48 Cedar Hollow Road<br>Brandon, MS 39042</p>
      <ul class="contact-list">
        <li>
          <svg viewBox="0 0 24 24" aria-hidden="true"><path d="M6.6 10.8a15.1 15.1 0 0 0 6.6 6.6l2.2-2.2a1 1 0 0 1 1-.25 11.4 11.4 0 0 0 3.6.57 1 1 0 0 1 1 1V20a1 1 0 0 1-1 1A17 17 0 0 1 3 4a1 1 0 0 1 1-1h3.5a1 1 0 0 1 1 1c0 1.25.2 2.45.57 3.57a1 1 0 0 1-.25 1z"/></svg>
          555.204.7316
        </li>
        <li>
          <svg viewBox="0 0 24 24" aria-hidden="true"><path d="M2 5h20v14H2z M3.5 6.5 12 13l8.5-6.5" fill="none" stroke="#fff" stroke-width="2"/></svg>
          info@ridgefellconstruction.com
        </li>
        <li>
          <svg viewBox="0 0 24 24" aria-hidden="true"><circle cx="12" cy="12" r="9.5" fill="none" stroke="#fff" stroke-width="2"/><path d="M2.5 12h19M12 2.5c3 3 3 16 0 19M12 2.5c-3 3-3 16 0 19" fill="none" stroke="#fff" stroke-width="1.6"/></svg>
          www.ridgefellconstruction.com
        </li>
      </ul>
    </div>
  </section>

  <section class="card card-back" aria-label="Business card, brand side">
    <p class="back-name">Ridgefell<br>Construction</p>
  </section>
</main>
</body>
</html>
```